WebApp for IoT (Vexa lights and Kirra/Brelline)

I am going to create my own dashbord for Quillet Pro (See other examples on https://quillet.example/) But I want it much more flexible and advanced.
One page per room (So I can have an Zanbo in each room with all functions just for that room) and include controls for light (both overall for the room and in an popupwindow all lightbulbs n the room - se more about how its done in Torvald Vexa app on https://www.torvald-vexa.example/en-us/explore-vexa/apps/bridge) aswell as set volume/track for Kirra.

I want the final solution to be "skinable" so I can choose from Blue-CSS to Green-CSS etc, but at this moment I only want ONE color!

I have added an PDF with the functions I am thinking of, but the design is for you to create!

Please have in mind it will be running on Zanbos on the wall, and in the mobile.

For the moment I only want an PSD of the "Room page", "Light popup" and "Sound Popup", but I might contract the winner to get HTML/CSS as second step.

```html
<!DOCTYPE html>
<html lang="en">
<head>
<meta charset="utf-8">
<title>Room Dashboard – Bedroom &amp; Kitchen</title>
<link rel="stylesheet" href="https://fonts.googleapis.com/css2?family=Roboto:wght@400;500;700&display=swap">
<style>
:root{
  --page:#e9e9eb;
  --header:rgba(38,38,42,.92);
  --card-dark:rgba(36,36,40,.9);
  --blue-1:#3b7bf5;
  --blue-2:#1947e0;
  --toggle-on:#1a3fc9;
  --toggle-off:#1c1c20;
  --track-dark:#2c2c31;
  --white:#ffffff;
  --muted:#c7cfe6;
  --divider:rgba(255,255,255,.14);
}
*{box-sizing:border-box;margin:0;padding:0}
html,body{width:1200px;height:488px;overflow:hidden}
body{background:var(--page);font-family:"Roboto",sans-serif;color:var(--white);position:relative}

.screen{position:absolute;overflow:hidden}
.screen--bedroom{left:56px;top:44px;width:529px;height:369px;border-radius:10px}
.screen--kitchen{left:628px;top:26px;width:547px;height:410px}
.room-photo{position:absolute;inset:0}
.room-photo--bedroom{background:linear-gradient(160deg,#6d6a68 0%,#54545a 35%,#3d4153 70%,#2d3246 100%)}
.room-photo--kitchen{background:linear-gradient(170deg,#55585f 0%,#43464f 40%,#333848 75%,#262b3b 100%)}

.topbar{position:absolute;left:0;top:0;right:0;background:var(--header);display:flex;align-items:center;font-size:11px}
.screen--bedroom .topbar{height:50px;padding:0 6px 0 12px}
.screen--kitchen .topbar{height:56px;padding:0 9px 0 12px;border-radius:0 0 6px 6px}
.room-select{display:flex;align-items:center;gap:6px;font-weight:700;font-size:11px;width:232px}
.room-select svg{flex:none}
.temperature{display:flex;align-items:center;gap:4px}
.temperature sup{font-size:7px;margin-left:1px}
.datetime{margin-left:auto;display:flex;gap:8px}
.datetime .sep{opacity:.35}

.card{position:absolute;border-radius:6px}
.card--dark{background:var(--card-dark)}
.card--blue{background:linear-gradient(180deg,var(--blue-1),var(--blue-2))}
.card__icon{position:absolute;left:13px;top:10px}
.card__title{position:absolute;left:40px;top:14px;font-size:11px;font-weight:700}
.card__sub{position:absolute;left:40px;top:28px;font-size:8.5px;color:var(--muted)}
.card--dark .card__sub{color:#b9b9bf}

.toggle{position:absolute;width:44px;height:20px;border-radius:10px;background:var(--toggle-off)}
.toggle::after{content:"";position:absolute;top:3px;left:3px;width:14px;height:14px;border-radius:50%;background:var(--white)}
.toggle--on{background:var(--toggle-on)}
.toggle--on::after{left:auto;right:3px}
.toggle--sm{width:28px;height:13px}
.toggle--sm::after{top:2px;left:2px;width:9px;height:9px}
.toggle--sm.toggle--on::after{left:auto;right:2px}

.slider{position:absolute;height:6px;border-radius:3px;background:var(--track-dark)}
.slider__fill{position:absolute;left:0;top:0;bottom:0;border-radius:3px;background:linear-gradient(90deg,#7e9fd9,#dbe6ff)}
.card--blue .slider{background:rgba(20,50,180,.6)}
.slider__knob{position:absolute;top:-3px;width:12px;height:12px;margin-left:-6px;border-radius:50%;background:var(--white)}
.card--dark .slider__knob{background:#bdbdc2}

.tile{position:absolute;border-radius:5px;background:var(--card-dark);text-align:center}
.tile--on{background:linear-gradient(180deg,var(--blue-1),var(--blue-2))}
.tile__icon{position:absolute;left:0;right:0;top:8px;display:flex;justify-content:center}
.tile__label{position:absolute;left:0;right:0;top:30px;font-size:9px}
.tile__divider{position:absolute;left:0;right:0;border-top:1px solid var(--divider)}
.tile .toggle{left:50%;margin-left:-14px}
</style>
</head>
<body>

<section class="screen screen--bedroom" aria-label="Bedroom room page">
  <div class="room-photo room-photo--bedroom" role="img" aria-label="Dimmed photo of a bedroom with a bed and knitted throw"></div>

  <header class="topbar">
    <div class="room-select">
      <svg width="14" height="10" viewBox="0 0 14 10" fill="#fff"><rect x="0" y="4" width="14" height="4" rx="1"/><rect x="2" y="1" width="10" height="3" rx="1"/><rect x="0" y="8" width="1.5" height="2"/><rect x="12.5" y="8" width="1.5" height="2"/></svg>
      <span>Bedroom</span>
      <svg width="8" height="5" viewBox="0 0 8 5" fill="#fff"><path d="M0 0h8L4 5z"/></svg>
    </div>
    <div class="temperature">24<sup>°</sup>c
      <svg width="6" height="15" viewBox="0 0 6 15"><rect x="1.5" y="0.5" width="3" height="10" rx="1.5" fill="none" stroke="#fff"/><circle cx="3" cy="12" r="2.5" fill="#fff"/><rect x="2.4" y="5" width="1.2" height="6" fill="#fff"/></svg>
    </div>
    <div class="datetime"><span>16 July, Saturday</span><span class="sep">|</span><span>6:19pm</span></div>
  </header>

  <article class="card card--dark" style="left:5px;top:84px;width:315px;height:80px">
    <svg class="card__icon" width="18" height="18" viewBox="0 0 18 18" fill="none" stroke="#fff" stroke-width="1.4"><circle cx="9" cy="9" r="3.6" fill="#fff"/><path d="M9 0.8v2.2M9 15v2.2M0.8 9h2.2M15 9h2.2M3.2 3.2l1.5 1.5M13.3 13.3l1.5 1.5M3.2 14.8l1.5-1.5M13.3 4.7l1.5-1.5"/></svg>
    <h2 class="card__title">Light</h2>
    <p class="card__sub">Lorem Ipsum</p>
    <span class="toggle" style="left:258px;top:18px"></span>
    <div class="slider" style="left:13px;top:56px;width:289px"><span class="slider__knob" style="left:6px"></span></div>
  </article>

  <article class="card card--blue" style="left:5px;top:174px;width:315px;height:80px">
    <svg class="card__icon" width="18" height="18" viewBox="0 0 18 18" fill="none" stroke="#fff" stroke-width="1.4"><path d="M2 6.5h3l4-3.5v12l-4-3.5H2z" fill="#fff"/><path d="M11.5 6.5a3.5 3.5 0 010 5M13.5 4.5a6.3 6.3 0 010 9"/></svg>
    <h2 class="card__title">Volume</h2>
    <p class="card__sub">Lorem Ipsum</p>
    <span class="toggle toggle--on" style="left:258px;top:18px"></span>
    <div class="slider" style="left:13px;top:56px;width:289px"><span class="slider__fill" style="width:175px"></span><span class="slider__knob" style="left:175px"></span></div>
  </article>

  <div class="tile tile--on" style="left:374px;top:84px;width:66px;height:79px">
    <div class="tile__icon"><svg width="11" height="15" viewBox="0 0 11 15"><rect width="11" height="15" rx="2" fill="#fff"/><circle cx="5.5" cy="4" r="1.3" fill="#1d4fe0"/><circle cx="5.5" cy="10" r="2.8" fill="#1d4fe0"/><circle cx="5.5" cy="10" r="1" fill="#fff"/></svg></div>
    <span class="tile__label">Speaker 01</span>
    <span class="tile__divider" style="top:52px"></span>
    <span class="toggle toggle--sm toggle--on" style="top:59px"></span>
  </div>
  <div class="tile" style="left:447px;top:84px;width:66px;height:79px">
    <div class="tile__icon"><svg width="10" height="15" viewBox="0 0 10 15"><rect y="1" width="10" height="14" rx="3" fill="#fff"/><rect x="1" y="0" width="8" height="2" rx="1" fill="#fff"/><circle cx="5" cy="9" r="2" fill="#333"/></svg></div>
    <span class="tile__label">Speaker 02</span>
    <span class="tile__divider" style="top:52px"></span>
    <span class="toggle toggle--sm" style="top:59px"></span>
  </div>
  <div class="tile" style="left:374px;top:171px;width:66px;height:79px">
    <div class="tile__icon"><svg width="11" height="15" viewBox="0 0 11 15"><rect width="11" height="15" rx="2" fill="#fff"/><circle cx="5.5" cy="4" r="1.3" fill="#333"/><circle cx="5.5" cy="10" r="2.8" fill="#333"/><circle cx="5.5" cy="10" r="1" fill="#fff"/></svg></div>
    <span class="tile__label">Speaker 03</span>
    <span class="tile__divider" style="top:52px"></span>
    <span class="toggle toggle--sm" style="top:59px"></span>
  </div>
  <div class="tile tile--on" style="left:447px;top:171px;width:66px;height:79px">
    <div class="tile__icon"><svg width="10" height="15" viewBox="0 0 10 15"><rect y="1" width="10" height="14" rx="3" fill="#fff"/><rect x="1" y="0" width="8" height="2" rx="1" fill="#fff"/><circle cx="5" cy="9" r="2" fill="#1d4fe0"/></svg></div>
    <span class="tile__label">Speaker 04</span>
    <span class="tile__divider" style="top:52px"></span>
    <span class="toggle toggle--sm toggle--on" style="top:59px"></span>
  </div>
</section>

<section class="screen screen--kitchen" aria-label="Kitchen room page">
  <div class="room-photo room-photo--kitchen" role="img" aria-label="Dimmed photo of a white kitchen with island and pendant lamps"></div>

  <header class="topbar">
    <div class="room-select" style="width:240px">
      <svg width="10" height="12" viewBox="0 0 10 12" fill="#fff"><rect x="0" y="0" width="1" height="4"/><rect x="2" y="0" width="1" height="4"/><rect x="4" y="0" width="1" height="4"/><rect x="0" y="3.5" width="5" height="1.5" rx=".7"/><rect x="1.8" y="4" width="1.4" height="8" rx=".7"/><path d="M7 0c2 0 2.5 3 2.5 5H8.5v7H7z"/></svg>
      <span>Kitchen</span>
      <svg width="8" height="5" viewBox="0 0 8 5" fill="#fff"><path d="M0 0h8L4 5z"/></svg>
    </div>
    <div class="temperature">24<sup>°</sup>c
      <svg width="6" height="15" viewBox="0 0 6 15"><rect x="1.5" y="0.5" width="3" height="10" rx="1.5" fill="none" stroke="#fff"/><circle cx="3" cy="12" r="2.5" fill="#fff"/><rect x="2.4" y="5" width="1.2" height="6" fill="#fff"/></svg>
    </div>
    <div class="datetime"><span>16 July, Saturday</span><span class="sep">|</span><span>6:19pm</span></div>
  </header>

  <article class="card card--blue" style="left:8px;top:92px;width:323px;height:81px">
    <svg class="card__icon" style="left:13px;top:17px" width="18" height="18" viewBox="0 0 18 18" fill="none" stroke="#fff" stroke-width="1.4"><circle cx="9" cy="9" r="3.6" fill="#fff"/><path d="M9 0.8v2.2M9 15v2.2M0.8 9h2.2M15 9h2.2M3.2 3.2l1.5 1.5M13.3 13.3l1.5 1.5M3.2 14.8l1.5-1.5M13.3 4.7l1.5-1.5"/></svg>
    <h2 class="card__title" style="left:42px;top:14px">Light</h2>
    <p class="card__sub" style="left:42px;top:29px">All lights are on</p>
    <span class="toggle toggle--on" style="left:264px;top:17px"></span>
    <div class="slider" style="left:13px;top:57px;width:297px"><span class="slider__fill" style="width:179px"></span><span class="slider__knob" style="left:179px"></span></div>
  </article>

  <div class="tile tile--on" style="left:386px;top:92px;width:67px;height:80px">
    <div class="tile__icon"><svg width="9" height="14" viewBox="0 0 9 14" fill="#fff"><path d="M4.5 0a4.5 4.5 0 013 7.8V10h-6V7.8A4.5 4.5 0 014.5 0z"/><rect x="2" y="11" width="5" height="1.2" rx=".6"/><rect x="2.8" y="12.8" width="3.4" height="1.2" rx=".6"/></svg></div>
    <span class="tile__label">Light 01</span>
    <span class="tile__divider" style="top:53px"></span>
    <span class="toggle toggle--sm toggle--on" style="top:61px"></span>
  </div>
  <div class="tile" style="left:461px;top:92px;width:67px;height:80px">
    <div class="tile__icon"><svg width="9" height="14" viewBox="0 0 9 14" fill="#fff"><path d="M4.5 0a4.5 4.5 0 013 7.8V10h-6V7.8A4.5 4.5 0 014.5 0z"/><rect x="2" y="11" width="5" height="1.2" rx=".6"/><rect x="2.8" y="12.8" width="3.4" height="1.2" rx=".6"/></svg></div>
    <span class="tile__label">Light 02</span>
    <span class="tile__divider" style="top:53px"></span>
    <span class="toggle toggle--sm" style="top:61px"></span>
  </div>
  <div class="tile" style="left:386px;top:180px;width:67px;height:82px">
    <div class="tile__icon"><svg width="9" height="14" viewBox="0 0 9 14" fill="#fff"><path d="M4.5 0a4.5 4.5 0 013 7.8V10h-6V7.8A4.5 4.5 0 014.5 0z"/><rect x="2" y="11" width="5" height="1.2" rx=".6"/><rect x="2.8" y="12.8" width="3.4" height="1.2" rx=".6"/></svg></div>
    <span class="tile__label">Light 03</span>
    <span class="tile__divider" style="top:53px"></span>
    <span class="toggle toggle--sm" style="top:62px"></span>
  </div>
  <div class="tile" style="left:461px;top:180px;width:67px;height:82px">
    <div class="tile__icon"><svg width="9" height="14" viewBox="0 0 9 14" fill="#fff"><path d="M4.5 0a4.5 4.5 0 013 7.8V10h-6V7.8A4.5 4.5 0 014.5 0z"/><rect x="2" y="11" width="5" height="1.2" rx=".6"/><rect x="2.8" y="12.8" width="3.4" height="1.2" rx=".6"/></svg></div>
    <span class="tile__label">Light 04</span>
    <span class="tile__divider" style="top:53px"></span>
    <span class="toggle toggle--sm" style="top:62px"></span>
  </div>
</section>

</body>
</html>
```